Healthcare and Professional IT Services Company need a redesigned business card

We are a IT Services company that targets small medical practices and professional business such as Attorneys, Accounts, Architects etc. We want to communicate a professional yet friendly image using recent logo redesign here on ArtHarbor. Like to see the colors blue and orange in the design. Must use the Tall Pine Computing as displayed in the new logo - then also want to incorporate the fish logo as well.

Target Market(s)

Small medical and professional services

Industry/Entity Type

It Company

Contact Information for Business Card

The usual stuff, place for name address phone website. Also maybe our tagline which is "Rooted in technology"

Requirements
Must have
• My new logo and the fish somewhere on the card

```html
<!DOCTYPE html>
<html lang="en">
<head>
<meta charset="utf-8">
<title>Tall Pine Computing – Business Card</title>
<link href="https://fonts.googleapis.com/css2?family=Open+Sans:ital,wght@0,400;0,600;0,700;1,700&display=swap" rel="stylesheet">
<style>
  :root {
    --backdrop: #3a332f;
    --card: #1d1d1f;
    --card-edge: #2a2a2d;
    --brand-blue: #1c9ad6;
    --accent-orange: #e8891c;
    --text-light: #f2f2f2;
    --divider: #8a8a8a;
  }
  * { margin: 0; padding: 0; box-sizing: border-box; }
  html, body {
    width: 1200px;
    height: 787px;
    overflow: hidden;
    background: var(--backdrop);
    font-family: "Open Sans", Arial, sans-serif;
  }
  .sheet {
    width: 1200px;
    height: 787px;
    display: flex;
    align-items: center;
    justify-content: center;
    gap: 40px;
  }
  .card {
    width: 540px;
    height: 309px;
    background: var(--card);
    border: 1px solid var(--card-edge);
    border-radius: 3px;
    box-shadow: 0 10px 30px rgba(0,0,0,.45);
    position: relative;
    overflow: hidden;
  }

  /* Brand lockup: name in one colour and weight, with one plain circle */
  .brand {
    display: flex;
    align-items: center;
    gap: 12px;
    color: var(--brand-blue);
    font-weight: 700;
  }
  .brand-dot {
    width: 18px;
    height: 18px;
    border-radius: 50%;
    background: var(--brand-blue);
    flex: none;
  }
  .brand-name { line-height: 1.05; }

  /* Front */
  .card-front {
    display: flex;
    flex-direction: column;
    justify-content: center;
    padding-left: 70px;
  }
  .card-front .brand-name { font-size: 34px; }
  .tagline {
    margin-top: 22px;
    margin-left: 30px;
    color: var(--text-light);
    font-style: italic;
    font-weight: 700;
    font-size: 17px;
  }

  /* Back */
  .card-back {
    display: flex;
    align-items: center;
  }
  .card-back .brand {
    width: 270px;
    padding-left: 34px;
  }
  .card-back .brand-name { font-size: 27px; }
  .divider {
    width: 1px;
    height: 200px;
    background: linear-gradient(to bottom, transparent, var(--divider) 30%, var(--divider) 70%, transparent);
  }
  .contact {
    padding-left: 22px;
    color: var(--text-light);
    font-size: 13.5px;
    line-height: 1.45;
  }
  .contact-name {
    color: var(--brand-blue);
    font-weight: 700;
    font-size: 17px;
    line-height: 1.2;
  }
  .contact-title {
    color: var(--accent-orange);
    font-weight: 600;
    font-size: 14px;
    margin-bottom: 8px;
  }
  .contact-address { margin-bottom: 6px; }
  .contact-line {
    display: flex;
    align-items: center;
    gap: 9px;
  }
  .contact-icon {
    width: 14px;
    height: 14px;
    flex: none;
    fill: var(--brand-blue);
  }
</style>
</head>
<body>
  <main class="sheet">
    <section class="card card-front" aria-label="Card front">
      <div class="brand">
        <span class="brand-dot"></span>
        <span class="brand-name">Tall Pine Computing</span>
      </div>
      <p class="tagline">Rooted in technology</p>
    </section>

    <section class="card card-back" aria-label="Card back">
      <div class="brand">
        <span class="brand-dot"></span>
        <span class="brand-name">Tall Pine<br>Computing</span>
      </div>
      <div class="divider"></div>
      <div class="contact">
        <p class="contact-name">Mark Ellison</p>
        <p class="contact-title">President</p>
        <p class="contact-address">2170 Harbor Lane<br>Cedar Vale, NY 11420</p>
        <p class="contact-line">
          <svg class="contact-icon" viewBox="0 0 16 16" aria-hidden="true"><path d="M3.5 1.5l2.5 3-1.5 1.6c.8 1.8 2.2 3.2 4 4l1.6-1.5 3 2.5-1.6 2.4C7 13.5 2.5 9 1.1 3.1z"/></svg>
          555 0142 7788
        </p>
        <p class="contact-line">
          <svg class="contact-icon" viewBox="0 0 16 16" aria-hidden="true"><path d="M1 3h14v10H1z M1.8 3.8L8 8.8l6.2-5z" fill-rule="evenodd"/></svg>
          mark@tallpine.com
        </p>
        <p class="contact-line">
          <svg class="contact-icon" viewBox="0 0 16 16" aria-hidden="true"><circle cx="8" cy="8" r="7"/><path d="M1 8h14M8 1c-2.5 3-2.5 11 0 14M8 1c2.5 3 2.5 11 0 14" stroke="#1d1d1f" stroke-width="1.1" fill="none"/></svg>
          www.tallpinecomputing.com
        </p>
      </div>
    </section>
  </main>
</body>
</html>
```